Design for a very long wall that will be wall printed. The name of the facility is "Brisk Gallery"

The space I am working on has a 30' x 8' wall. It is a wall that is located in a under construction Design Showroom where contractors of all trades can have an office and put out their banners and different items for customers to come and see. so there could be roofers, construction, cabinet installers and designers, gutters and other trades can rent an office in the space and bring their customers and sit down and talk about what they need. I want the design for the wall to have a bold punch and it will be printed on the wall with a high definition wall printer. The walls are arctic white right now and I can send the color codes for the color the wall is currently. The wall printer has the capability to do white as well. I am including some pics of the space and an example wall print.

Target Market(s)

Contractors and Customers of Contractors

Industry/Entity Type

all trades. Photos are to demonstrate the capabilities of the printer that will be used

Requirements
Must have
• Perhaps have a person or persons int he design, a human element and perhaps some abstract elements as well
Nice to have
• Perhaps some architecture or perhaps an interior cabinet or fixtures. Glass doors and or walls. Perhaps incorporate the name "Brisk Gallery"

```html
<!DOCTYPE html>
<html lang="en">
<head>
<meta charset="utf-8">
<title>Brisk Gallery Wall Banner</title>
<link rel="stylesheet" href="https://fonts.googleapis.com/css2?family=Montserrat:wght@700&display=swap">
<style>
  :root {
    --stage: #333333;
    --paper: #ffffff;
    --orange: #f79700;
    --navy: #141a33;
    --photo-light: #f0ece6;
    --photo-warm: #d9a05a;
  }
  html, body {
    margin: 0;
    padding: 0;
    width: 1200px;
    height: 1200px;
    overflow: hidden;
    background: var(--stage);
  }
  .wall-banner {
    position: absolute;
    left: 69px;
    top: 462px;
    width: 1063px;
    height: 283px;
    display: block;
  }
  .banner-bg { fill: var(--paper); }
  .accent-block { fill: var(--orange); }
  .cross-mark { stroke: var(--navy); stroke-width: 6; stroke-linecap: butt; }
  .dot { fill: var(--navy); }
  .facility-name {
    font-family: "Montserrat", sans-serif;
    font-weight: 700;
    font-size: 60px;
    fill: var(--orange);
    stroke: var(--navy);
    stroke-width: 1.6;
    paint-order: stroke fill;
  }
</style>
</head>
<body>
<svg class="wall-banner" viewBox="0 0 1329 354" xmlns="http://www.w3.org/2000/svg">
  <defs>
    <linearGradient id="photoTone" x1="0" y1="0" x2="0" y2="1">
      <stop offset="0" stop-color="var(--photo-light)"/>
      <stop offset="0.6" stop-color="#ece4da"/>
      <stop offset="1" stop-color="var(--photo-warm)"/>
    </linearGradient>
  </defs>

  <rect class="banner-bg" x="0" y="0" width="1329" height="354"/>

  <!-- frame blocks -->
  <rect class="accent-block" x="0" y="0" width="221" height="48"/>
  <rect class="accent-block" x="0" y="0" width="48" height="354"/>
  <rect class="accent-block" x="0" y="306" width="694" height="48"/>
  <rect class="accent-block" x="840" y="288" width="489" height="66"/>

  <!-- worker photo -->
  <path role="img" aria-label="Photo of a smiling tradeswoman in a white t-shirt, work gloves and orange tool belt, making a call-me gesture"
        d="M534 7 H652 V110 H684 V354 H510 V190 H426 V62 H534 Z" fill="url(#photoTone)"/>

  <!-- cross marks -->
  <g class="cross-row">
    <path class="cross-mark" d="M265 12 L293 40 M293 12 L265 40"/>
    <path class="cross-mark" d="M335 12 L363 40 M363 12 L335 40"/>
    <path class="cross-mark" d="M405 12 L433 40 M433 12 L405 40"/>
    <path class="cross-mark" d="M475 12 L503 40 M503 12 L475 40"/>
  </g>

  <!-- bottom square dots -->
  <g class="dot-scatter">
    <rect class="dot" x="433" y="294" width="12" height="12"/>
    <rect class="dot" x="488" y="294" width="12" height="12"/>
    <rect class="dot" x="488" y="324" width="12" height="12"/>
    <rect class="dot" x="713" y="294" width="12" height="12"/>
    <rect class="dot" x="713" y="324" width="12" height="12"/>
    <rect class="dot" x="768" y="324" width="12" height="12"/>
  </g>

  <!-- top-right dot triangle -->
  <g class="dot-grid">
    <rect class="dot" x="1129" y="25" width="6" height="6"/>
    <rect class="dot" x="1159" y="25" width="6" height="6"/>
    <rect class="dot" x="1159" y="43" width="6" height="6"/>
    <rect class="dot" x="1189" y="25" width="6" height="6"/>
    <rect class="dot" x="1189" y="43" width="6" height="6"/>
    <rect class="dot" x="1189" y="61" width="6" height="6"/>
    <rect class="dot" x="1219" y="25" width="6" height="6"/>
    <rect class="dot" x="1219" y="43" width="6" height="6"/>
    <rect class="dot" x="1219" y="61" width="6" height="6"/>
    <rect class="dot" x="1219" y="79" width="6" height="6"/>
    <rect class="dot" x="1249" y="25" width="6" height="6"/>
    <rect class="dot" x="1249" y="43" width="6" height="6"/>
    <rect class="dot" x="1249" y="61" width="6" height="6"/>
    <rect class="dot" x="1249" y="79" width="6" height="6"/>
    <rect class="dot" x="1249" y="97" width="6" height="6"/>
    <rect class="dot" x="1279" y="25" width="6" height="6"/>
    <rect class="dot" x="1279" y="43" width="6" height="6"/>
    <rect class="dot" x="1279" y="61" width="6" height="6"/>
    <rect class="dot" x="1279" y="79" width="6" height="6"/>
    <rect class="dot" x="1279" y="97" width="6" height="6"/>
    <rect class="dot" x="1279" y="115" width="6" height="6"/>
  </g>

  <text class="facility-name" x="1319" y="270" text-anchor="end">Brisk Gallery</text>
</svg>
</body>
</html>
```